Provide bookkeeping and accounting services to small and growing businesses

We need website and logo design using the name Dornaby as the logo.
The target audience are small companies and startups who need:
1) Simple bookkeeping services
2) Accounting advice that only someone with many years of senior financial experience as a CPA can provide.

The services are provided by two individuals. each of whom specialize in one of the areas.

We want the website to be clean without a lot of visual distraction but don't know how to make a boring subject interesting. We believe our potential clients, small business owners, need to find what they want quickly and easily without a lot of verbiage or distractions.

We've attached a draft of the homepage and have completed the text on most of the other pages.

Target Market(s)

small and early stage growth companies in San Diego North County

Industry/Entity Type

Accounting

Number of Pages Required

1 page

Font styles to use
Sans Serif

Colors
86cfc6
33b8a4
85cae6

Requirements
Must have
• We need a design for the website homepage that includes the name Dornaby as the logo. Must include a design for the name.
• Must have color in teal or greenish blue.
Nice to have
• White background, clean, clear, uncluttered.
• We would like to use the design in a Theme on a WordPress website. Themes Paper Lantern and Quiet Harbour are appealing to us.
Should not have
• Moving pictures

```html
<!DOCTYPE html>
<html lang="en">
<head>
<meta charset="utf-8">
<title>Dornaby — Accounting and Bookkeeping</title>
<link rel="stylesheet" href="https://fonts.googleapis.com/css2?family=Cinzel:wght@400&family=Open+Sans:wght@400;600&family=Raleway:wght@300;400&display=swap">
<style>
:root{
  --teal:#33b8a4;
  --teal-soft:#86cfc6;
  --teal-panel:rgba(51,184,164,.82);
  --ink:#4a4a4a;
  --text:#6b6b6b;
  --nav:#6f6f6f;
  --white:#ffffff;
}
*{margin:0;padding:0;box-sizing:border-box}
html,body{width:1080px;height:1200px;overflow:hidden;background:var(--white)}
body{position:relative;font-family:"Open Sans",sans-serif;color:var(--text)}

.top-rule{position:absolute;left:0;top:0;width:1080px;height:2px;background:var(--teal)}

.site-header{position:absolute;left:0;top:2px;width:1080px;height:90px}
.brand{position:absolute;left:88px;top:20px;color:var(--teal);font-family:"Cinzel",serif;font-weight:400}
.brand-name{font-size:31px;line-height:34px;letter-spacing:1px}
.brand-tag{font-size:8.5px;letter-spacing:1.6px;margin-top:2px}

.main-nav{position:absolute;top:37px;left:0;width:1080px;font-size:13px;line-height:16px}
.main-nav a{position:absolute;color:var(--nav);text-decoration:none;white-space:nowrap}
.main-nav a.is-current{color:var(--teal)}

.hero{position:absolute;left:0;top:92px;width:1080px;height:462px;overflow:hidden;
  background:linear-gradient(160deg,#5d5f63 0%,#8c8a86 30%,#b9b2a8 55%,#8d8177 78%,#5c5048 100%)}
.hero-panel{position:absolute;left:121px;top:155px;width:551px;height:159px;background:var(--teal-panel);color:var(--white);font-family:"Raleway",sans-serif}
.hero-title{position:absolute;left:29px;top:20px;font-weight:300;font-size:41px;line-height:46px;letter-spacing:.5px}
.hero-lead{position:absolute;left:32px;top:73px;font-weight:400;font-size:22px;line-height:28px}
.hero-arrow{position:absolute;top:215px;width:32px;height:32px}
.hero-arrow.prev{left:29px}
.hero-arrow.next{left:1018px}
.hero-shade{position:absolute;left:0;top:554px;width:1080px;height:24px;background:radial-gradient(ellipse at 50% 0,rgba(0,0,0,.09),rgba(0,0,0,0) 70%)}

.welcome{position:absolute;left:0;top:602px;width:1080px;text-align:center}
.welcome h1{font-family:"Cinzel",serif;font-weight:400;font-size:29px;line-height:34px;color:var(--ink)}
.welcome h2{font-family:"Cinzel",serif;font-weight:400;font-size:20.5px;line-height:26px;color:var(--teal)}
.welcome p{width:680px;margin:6px auto 0;font-size:11.2px;line-height:19px;color:var(--text)}

.service{position:absolute;top:740px;width:275px;text-align:center}
.service-photo{display:block;width:275px;height:171px;box-shadow:0 6px 8px -6px rgba(0,0,0,.25)}
.service h3{margin-top:22px;font-weight:400;font-size:16px;line-height:20px;color:#444;letter-spacing:.2px}
.service.is-active h3{color:var(--teal)}
.service p{width:265px;margin:5px auto 0;font-size:11.2px;line-height:18.7px;color:var(--text)}
.service .rule{position:absolute;left:0;top:296px;width:275px;height:2px;background:var(--teal-soft)}
.service.is-active .rule{background:var(--teal)}

.site-footer{position:absolute;left:0;top:1097px;width:1080px;height:103px;background:var(--teal);color:var(--white);text-align:center}
.contact-links{position:absolute;left:0;top:0;width:1080px;height:60px}
.contact-links svg{position:absolute;top:28px;width:18px;height:18px;fill:none;stroke:var(--white);stroke-width:1.8;stroke-linecap:round;stroke-linejoin:round}
.copyright{position:absolute;left:0;top:59px;width:1080px;font-size:12.6px;line-height:16px}
</style>
</head>
<body>
<div class="top-rule"></div>

<header class="site-header">
  <div class="brand">
    <div class="brand-name">Dornaby</div>
    <div class="brand-tag">Accounting and Bookkeeping</div>
  </div>
  <nav class="main-nav">
    <a class="is-current" style="left:448px">Home</a>
    <a style="left:528px">About Us</a>
    <a style="left:626px">Services</a>
    <a style="left:718px">Experience</a>
    <a style="left:826px">Resources</a>
    <a style="left:930px">Contact Us</a>
  </nav>
</header>

<section class="hero" role="img" aria-label="Photo of business people reviewing financial charts at a desk">
  <div class="hero-panel">
    <div class="hero-title">DORNABY</div>
    <div class="hero-lead">We simple book keeping services, financial<br>&amp; accounting advice for small start up companies.</div>
  </div>
  <svg class="hero-arrow prev" viewBox="0 0 32 32"><circle cx="16" cy="16" r="14.5" fill="none" stroke="rgba(255,255,255,.55)" stroke-width="2"/><path d="M18 10l-6 6 6 6" fill="none" stroke="rgba(255,255,255,.6)" stroke-width="2"/></svg>
  <svg class="hero-arrow next" viewBox="0 0 32 32"><circle cx="16" cy="16" r="14.5" fill="none" stroke="rgba(255,255,255,.55)" stroke-width="2"/><path d="M14 10l6 6-6 6" fill="none" stroke="rgba(255,255,255,.6)" stroke-width="2"/></svg>
</section>
<div class="hero-shade"></div>

<section class="welcome">
  <h1>Welcome To Dornaby</h1>
  <h2>We are Accounting and Bookkeeping</h2>
  <p>Dornaby offers a flexible range of accounting and bookkeeping services and support for small and growing organizations in San Diego North County. We provide bookkeeping services specializing in LedgerBooks® at your offices or remotely from ours.</p>
</section>

<article class="service is-active" style="left:89px">
  <div class="service-photo" role="img" aria-label="Photo of hands leafing through office binders" style="background:linear-gradient(135deg,#f1d6dc 0%,#e9e6e6 45%,#cfd2d6 100%)"></div>
  <h3>BOOKKEEPING SERVICES</h3>
  <p>It is a long established fact that a reader will be distracted by the readable content of a page when looking at its layout. The point of using Lorem</p>
  <div class="rule"></div>
</article>

<article class="service" style="left:402px">
  <div class="service-photo" role="img" aria-label="Photo of seedlings growing from stacks of gold coins in soil" style="background:linear-gradient(180deg,#9fb84a 0%,#7a8a2e 40%,#a5842f 65%,#3d3025 100%)"></div>
  <h3>ACCOUNTING SUPPORT</h3>
  <p>It is a long established fact that a reader will be distracted by the readable content of a page when looking at its layout. The point of using Lorem</p>
  <div class="rule"></div>
</article>

<article class="service" style="left:716px">
  <div class="service-photo" role="img" aria-label="Photo of an advisor with a calculator meeting clients" style="background:linear-gradient(90deg,#dcd3cc 0%,#f3f1ee 40%,#ece9e6 70%,#c9ccd2 100%)"></div>
  <h3>BUSINESS ADVICE</h3>
  <p>It is a long established fact that a reader will be distracted by the readable content of a page when looking at its layout. The point of using Lorem</p>
  <div class="rule"></div>
</article>

<footer class="site-footer">
  <nav class="contact-links" aria-label="Contact links">
    <svg style="left:413px" viewBox="0 0 18 18" aria-label="Email"><rect x="1.5" y="3.5" width="15" height="11" rx="1"/><path d="M2 4.5l7 5.5 7-5.5"/></svg>
    <svg style="left:449px" viewBox="0 0 18 18" aria-label="Phone"><path d="M4 2h3l1.5 4-2 1.3a9 9 0 0 0 4.2 4.2L12 9.5l4 1.5v3a2 2 0 0 1-2 2A13 13 0 0 1 2 4a2 2 0 0 1 2-2z"/></svg>
    <svg style="left:489px" viewBox="0 0 18 18" aria-label="Office location"><path d="M9 16.5s-5.5-5.2-5.5-9a5.5 5.5 0 0 1 11 0c0 3.8-5.5 9-5.5 9z"/><circle cx="9" cy="7.5" r="2"/></svg>
    <svg style="left:525px" viewBox="0 0 18 18" aria-label="Chat"><path d="M2 3.5h14v9H7l-3.5 3v-3H2z"/></svg>
    <svg style="left:564px" viewBox="0 0 18 18" aria-label="Website"><circle cx="9" cy="9" r="7.2"/><path d="M1.8 9h14.4M9 1.8c2.2 2 2.2 12.4 0 14.4M9 1.8c-2.2 2-2.2 12.4 0 14.4"/></svg>
    <svg style="left:605px" viewBox="0 0 18 18" aria-label="Share"><circle cx="13.5" cy="4" r="2.2"/><circle cx="4.5" cy="9" r="2.2"/><circle cx="13.5" cy="14" r="2.2"/><path d="M6.5 8l5-2.8M6.5 10l5 2.8"/></svg>
    <svg style="left:645px" viewBox="0 0 18 18" aria-label="Newsletter"><rect x="2" y="2" width="14" height="14" rx="1.5"/><path d="M5 6h8M5 9h8M5 12h5"/></svg>
  </nav>
  <div class="copyright">Copyrights@2016 Company name , All rights Reserved</div>
</footer>
</body>
</html>
```